Business Card Design Project

Looking for a simple and stylish business card. We are an Advertising Company. The card Must feature the company logo (attached) and also this info.
p: 0481552306
e: sales@rt-media.com.au
w: www.rt-media.com.au
We Advertise mainly using TV screens featured in restaurants and cafe. See website for more about the business.
Not really looking for a plain background, but at the same time do not want to much happening in the Background. I am not really to fussy though with the design or the colour scheme, and I am leaving the creativity part up to you creative designers.

```html
<!DOCTYPE html>
<html lang="en">
<head>
<meta charset="utf-8">
<title>RTMEDIA Business Card</title>
<link rel="stylesheet" href="https://fonts.googleapis.com/css2?family=Questrial&display=swap">
<style>
  :root {
    --stage-light: #f7f3ec;
    --stage-dark: #d6cfc6;
    --card-white: #ffffff;
    --brand-pink: #e31d5c;
    --brand-blue: #164d99;
    --text-white: #ffffff;
  }
  html, body {
    margin: 0;
    padding: 0;
    width: 1200px;
    height: 900px;
    overflow: hidden;
  }
  body {
    position: relative;
    background: radial-gradient(ellipse at 50% 45%, var(--stage-light) 0%, #ece6dd 55%, var(--stage-dark) 100%);
    font-family: "Questrial", "Helvetica Neue", Arial, sans-serif;
  }
  .business-card {
    position: absolute;
    left: 422px;
    top: 139px;
    width: 355px;
    height: 621px;
    background: var(--card-white);
    overflow: hidden;
  }
  .card-graphics {
    position: absolute;
    inset: 0;
    width: 355px;
    height: 621px;
  }
  .stripe { fill: var(--brand-pink); }
  .blue-field { fill: var(--brand-blue); }
  .title-text {
    fill: var(--text-white);
    font-family: "Questrial", "Helvetica Neue", Arial, sans-serif;
    font-size: 25px;
  }
  .company-name {
    position: absolute;
    left: 30px;
    top: 22px;
    margin: 0;
    font-size: 64px;
    font-weight: 400;
    line-height: 1;
    letter-spacing: 1px;
    color: var(--brand-blue);
  }
  .contact-list {
    position: absolute;
    left: 30px;
    top: 494px;
    margin: 0;
    padding: 0;
    list-style: none;
    color: var(--text-white);
    font-size: 24px;
    line-height: 34px;
  }
</style>
</head>
<body>
  <div class="business-card">
    <svg class="card-graphics" viewBox="0 0 355 621" aria-hidden="false">
      <polygon class="stripe" points="0,254 355,107 355,129 0,277"/>
      <polygon class="stripe" points="0,303 355,156 355,197 0,344"/>
      <polygon class="stripe" points="0,362 355,215 355,298 0,446"/>
      <polygon class="stripe" points="0,460 355,310 355,336 0,486"/>
      <polygon class="blue-field" points="0,486 355,336 355,621 0,621"/>
      <polygon class="stripe" points="246,621 355,574 355,621"/>
      <g class="title-block" transform="translate(250,291) rotate(-22.5)">
        <text class="title-text" x="0" y="0" text-anchor="end">Managing Director</text>
        <text class="title-text" x="33" y="34" text-anchor="end">Mark Delaney</text>
      </g>
    </svg>
    <h1 class="company-name">RTMEDIA</h1>
    <ul class="contact-list">
      <li class="contact-phone">0481552306</li>
      <li class="contact-email">sales@rt-media.com.au</li>
      <li class="contact-web">www.rt-media.com.au</li>
    </ul>
  </div>
</body>
</html>
```